Morvane Capital, a private equity fund, needs a brochure

Morvane Capital is a private equity fund dedicated to the development of budget hotels in France (reasonably priced hotel rooms).
Our customers are French private and high-income investors.

The brochure should communicate :
- seriousness and expertise
- trust, confidence and security
- financial product and profitability

The title is : Investissez dans l'hôtellerie économique et l'immobilier

Brochure size :
3 pages A4
Open size : 63 x 29,7 cm
Closed size : 21 x 29,7 cm

Our competitors :
Trelisse http://trelisse-immo-horizon.example/
789 Parcours http://www.789parcours.example/
GLD Capital http://www.gldam.example/
Soltane capital http://www.soltanecapital.example/
Barostel http://www.barostel.example/

Target Market(s)

Private investors, high-income ; Institutional investors ; Target customers are French private investors with high revenue.

Industry/Entity Type

Financial

Requirements
Must have
• - Brochure must respect our identity (you can see our logo) and use its colors and typo (and/or same typo style)
- You must use pictures on each interior pages (pictures of projetc and hotels)

```html
<!DOCTYPE html>
<html lang="fr">
<head>
<meta charset="utf-8">
<title>Morvane Capital — Brochure</title>
<link href="https://fonts.googleapis.com/css2?family=PT+Serif:wght@400;700&family=Open+Sans:wght@400;600;700&display=swap" rel="stylesheet">
<style>
:root{
  --red:#a8202c;
  --red-panel:#a51f2b;
  --ink:#2b2b2b;
  --grey:#8d9096;
  --grey-light:#c9cbce;
  --paper:#ffffff;
  --backdrop:#ecebe8;
}
*{margin:0;padding:0;box-sizing:border-box}
html,body{width:1200px;height:721px;overflow:hidden;background:var(--backdrop)}
body{position:relative;font-family:"Open Sans",sans-serif;color:var(--ink)}
.brochure{position:absolute;left:15px;top:78px;width:1170px;height:566px;background:var(--paper);box-shadow:0 2px 8px rgba(0,0,0,.18)}
.panel{position:absolute;top:0;height:100%}
.panel-1{left:0;width:243px}
.panel-2{left:243px;width:172px;background:var(--red-panel);color:#fff}
.panel-3{left:415px;width:340px}
.panel-4{left:755px;width:415px}
.abs{position:absolute}
h2{font-family:"PT Serif",serif;font-weight:700;color:var(--red);font-size:12.5px;line-height:14px}
.panel-2 h2{color:#fff}
h3{font-family:"PT Serif",serif;font-weight:700;color:var(--red);font-size:11px;line-height:13px}
p,li{font-size:5.3px;line-height:6.6px}
.bold{font-weight:700}
.bullets{list-style:none}
.bullets li{position:relative;padding-left:14px;font-weight:700;margin-bottom:8px;font-size:5.6px}
.bullets li::before{content:"";position:absolute;left:0;top:0;width:3px;height:9px;background:var(--red)}
.panel-2 .bullets li::before{background:#fff}
.justify{text-align:justify}
.photo{background:linear-gradient(135deg,#8a8f96 0%,#c7cdd3 45%,#5d6168 100%)}
.red-box{background:var(--red);color:#fff;font-size:5.3px;line-height:6.6px;padding:5px}
.risk-title{color:var(--red);font-weight:700}
.chart-title{font-size:5.6px;font-weight:700;color:#555;white-space:nowrap}
.gain-bar{background:var(--red);color:#fff;font:700 15px "Open Sans",sans-serif;display:flex;align-items:center;justify-content:center}
.gain-label{background:var(--grey);color:#fff;font:600 5.4px "Open Sans",sans-serif;display:flex;align-items:center;justify-content:center}
.gain-class{border:1px solid var(--grey-light);font:600 4.8px "Open Sans",sans-serif;display:flex;align-items:center;justify-content:center;color:#555}
table.fees{border-collapse:collapse}
table.fees td{border:1px solid #bdbdbd;width:64px;height:11.5px}
</style>
</head>
<body>
<div class="brochure">

  <section class="panel panel-1">
    <h2 class="abs" style="left:28px;top:30px;width:200px">Des investissements centrés sur l'hôtellerie et l'immobilier</h2>
    <p class="abs justify" style="left:28px;top:64px;width:200px">Morvane Capital a pour objectif d'accueillir jusqu'à 30 millions d'euros de souscriptions sur 2 ans. Le produit de ces souscriptions permettra la prise de participations minoritaires (40% maximum) dans le capital de sociétés ayant pour objet :</p>
    <ul class="bullets abs" style="left:36px;top:110px;width:180px">
      <li>La construction ou l'acquisition d'hôtels économiques et leur exploitation.</li>
      <li>La construction ou l'acquisition de meublés de tourisme et leur exploitation.</li>
      <li>La construction-vente d'immeuble en VEFA.</li>
    </ul>
    <div class="photo abs" role="img" aria-label="Photographie d'un hôtel économique moderne en façade" style="left:34px;top:187px;width:202px;height:120px"></div>
    <h2 class="abs" style="left:28px;top:328px;width:205px">Un partenariat avec<br>BRÉVANNE HOTELS GROUP</h2>
    <p class="abs justify" style="left:28px;top:364px;width:200px">Pour l'exploitation des investissements hôteliers, les sociétés du portefeuille interviendront en partenariat avec un opérateur hôtelier – BRÉVANNE HOTELS GROUP – dans le cadre d'un accord de franchise (Brévanne Hotels Group, 2ème opérateur d'Europe, plus de 1000 hôtels dans le monde).</p>
    <ul class="bullets abs" style="left:36px;top:422px;width:180px">
      <li>Contrats de franchise sous enseignes : Étape Bleue **, Carillon *** et Lys Inn ***.</li>
      <li>Contrats d'assistance technique.</li>
      <li>Implantation de plus de 12 hôtels dans 6 régions françaises d'outremer.</li>
    </ul>
  </section>

  <section class="panel panel-2">
    <h2 class="abs" style="left:14px;top:24px;width:150px">Pourquoi l'hôtellerie et l'immobilier ?</h2>
    <p class="abs justify" style="left:14px;top:62px;width:148px">Dans des conditions économiques et financières perturbées depuis la crise financière de 2008, les investisseurs exigent aujourd'hui des placements structurés pour résister aux effets économiques induits. Selon l'analyse des équipes de Morvane Capital, le marché de l'hôtellerie économique en croissance depuis sa création répond particulièrement bien à ces attentes. Ce positionnement est en adéquation avec la baisse des budgets alloués aux déplacements et voyages professionnels et touristiques.</p>
    <p class="abs justify" style="left:14px;top:128px;width:148px">Le marché de l'immobilier reste quant à lui une valeur refuge en temps de crise, selon l'analyse des équipes de Morvane Capital.</p>
    <ul class="bullets abs" style="left:16px;top:180px;width:148px">
      <li>Un marché en croissance malgré la crise.</li>
      <li>Sur 2011, la croissance cumulée du nombre de nuitées atteint + 3,2% par rapport à 2010. (source KDLS).</li>
      <li>Secteur porteur. 1,5 milliard d'euros ont été investis dans le secteur de l'hôtellerie en France en 2011. (source KDLS).</li>
    </ul>
    <h2 class="abs" style="left:12px;top:252px;width:160px;font-size:11.8px;line-height:13.5px">Focus sur l'hôtellerie économique dans les régions françaises ultramarines</h2>
    <p class="abs justify" style="left:14px;top:308px;width:148px">Le marché des hôtels économiques normés et standardisés sous enseigne nationale ou internationale est peu développé dans les DOM-COM. Ces régions sont équipées principalement d'hôtels balnéaires à vocation touristique essentiellement implantés sur des lieux géographiques éloignés des centres économiques. Depuis une vingtaine d'années, le développement important des populations et la centralisation des zones commerciales et industrielles sur les capitales administratives ont généré d'importants embouteillages qui compliquent les accès à ces zones. L'offre hôtelière n'est plus en adéquation avec les attentes des visiteurs professionnels. La création d'une chaîne d'hôtels économiques est la réponse à ce besoin et bénéficie de l'appui de la puissance publique et des instances régionales.</p>
    <ul class="bullets abs" style="left:16px;top:436px;width:148px">
      <li>Absence d'hôtels économiques standardisés et normés dans ces régions.</li>
      <li>Structures hôtelières existantes inadaptées aux besoins du marché professionnel et coûteuses : prix des nuitées proposées par ces nouveaux hôtels inférieurs de 30 à 50% aux prix pratiqués localement.</li>
      <li>Programmes d'investissements bénéficiant d'avantages fiscaux, sociaux et de subventions.</li>
    </ul>
  </section>

  <section class="panel panel-3">
    <h2 class="abs" style="left:30px;top:16px;width:300px">Immobilier, valeur refuge pour l'investisseur (selon l'analyse de Morvane Capital)</h2>
    <ul class="bullets abs" style="left:30px;top:52px;width:300px">
      <li>Un investissement dans la pierre.</li>
      <li>Une réponse à l'incertitude des marchés financiers et de la monnaie et des risques d'inflation.</li>
      <li>Des emplacements exceptionnels (centres villes, aéroports, zones commerciales).</li>
    </ul>
    <h2 class="abs" style="left:30px;top:104px;width:300px">Trois sources potentielles de gains :</h2>
    <p class="abs justify" style="left:30px;top:126px;width:144px">Une double plus-value potentielle hôtelière et immobilière assortie d'un rendement annuel. La création de valeur pour chacun des hôtels dans lesquels Morvane Capital prendra des participations proviendra de la valorisation des murs de l'hôtel, de la valorisation de son fonds de commerce et de la rentabilité annuelle de l'exploitation. L'activité de location de meublés de tourisme bénéficie des mêmes synergies.</p>
    <p class="abs justify" style="left:184px;top:126px;width:144px">La création de valeur pour l'activité de promotion immobilière (construction vente des immeubles) proviendra des marges dégagées par les opérations de promotion</p>
    <div class="red-box abs" style="left:30px;top:186px;width:98px;height:28px">Trois sources potentielles de gains, assorties toutefois d'un risque de perte en capital</div>
    <div class="red-box abs" style="left:132px;top:186px;width:102px;height:28px">Atténuation de risques du fait de l'investissement diversifié dans les murs et dans le fonds de commerce</div>
    <div class="red-box abs" style="left:238px;top:186px;width:90px;height:28px">Un recours à un financement peu coûteux</div>
    <p class="abs bold" style="left:72px;top:224px;font-size:5.4px">Plus-values hôtelières.</p>
    <p class="abs bold" style="left:136px;top:224px;font-size:5.4px">Plus-values immobilières.</p>
    <p class="abs bold" style="left:210px;top:224px;font-size:5.4px">Rendement annuel capitalisé.</p>
    <svg class="abs" style="left:22px;top:236px" width="160" height="72" viewBox="0 0 160 72" aria-label="Schéma des gains espérés sur la période d'investissement">
      <polygon points="4,48 120,6 120,48" fill="#f0e4e5"/>
      <rect x="66" y="26" width="42" height="16" fill="#fff" stroke="#d9a6aa" stroke-width=".5"/>
      <text x="87" y="33" font-size="3.6" text-anchor="middle" fill="#8a1b25" font-family="Open Sans,sans-serif">Espérance de gain</text>
      <text x="87" y="38" font-size="3.6" text-anchor="middle" fill="#8a1b25" font-family="Open Sans,sans-serif">pour l'investisseur</text>
      <rect x="120" y="8" width="36" height="9" fill="#7d8aa8"/>
      <rect x="120" y="19" width="36" height="9" fill="#7d8aa8"/>
      <rect x="120" y="30" width="36" height="11" fill="#2f3f6a"/>
      <text x="138" y="14" font-size="3" text-anchor="middle" fill="#fff" font-family="Open Sans,sans-serif">Plus-values hôtelières</text>
      <text x="138" y="25" font-size="3" text-anchor="middle" fill="#fff" font-family="Open Sans,sans-serif">Plus-values immobilières</text>
      <text x="138" y="37" font-size="3" text-anchor="middle" fill="#fff" font-family="Open Sans,sans-serif">Rendement capitalisé</text>
      <rect x="4" y="44" width="50" height="8" fill="#a8202c"/>
      <text x="8" y="49.5" font-size="3.4" fill="#fff" font-family="Open Sans,sans-serif">Investissements</text>
      <rect x="112" y="44" width="44" height="8" fill="#a8202c"/>
      <text x="116" y="49.5" font-size="3.2" fill="#fff" font-family="Open Sans,sans-serif">Remboursement du capital</text>
      <line x1="4" y1="53" x2="156" y2="53" stroke="#555" stroke-width=".6"/>
      <g font-size="3.6" fill="#fff" font-family="Open Sans,sans-serif">
        <rect x="8" y="62" width="14" height="7" fill="#6b6f76"/><text x="10" y="67">2012</text>
        <rect x="24" y="62" width="14" height="7" fill="#6b6f76"/><text x="26" y="67">2013</text>
        <rect x="40" y="62" width="14" height="7" fill="#6b6f76"/><text x="42" y="67">2014</text>
        <rect x="80" y="62" width="14" height="7" fill="#6b6f76"/><text x="82" y="67">2017</text>
        <rect x="112" y="62" width="14" height="7" fill="#6b6f76"/><text x="114" y="67">2019</text>
      </g>
    </svg>
    <p class="abs justify" style="left:188px;top:240px;width:142px">L'attention des investisseurs est toutefois attirée sur l'impact de l'effet "moyenne" d'un tel affichage, lequel peut masquer de mauvais résultats pour certains fonds en particulier et lequel ne préjuge pas de performances d'un niveau équivalent pour le présent fond (étant en toutes hypothèses rappelé que Morvane Capital présente un risque de perte en capital). Par ailleurs, l'attention des investisseurs est attirée sur les facteurs de risques liés à un investissement dans Morvane Capital présentés ci-après dans le présent document</p>
    <h2 class="abs" style="left:24px;top:358px;width:220px">Comment sont répartis les gains ?</h2>
    <p class="abs justify" style="left:30px;top:378px;width:216px">Le capital de la société Morvane Capital est constitué de deux types de catégorie d'actions A et B.</p>
    <ul class="bullets abs" style="left:30px;top:394px;width:216px">
      <li>Les actions de type A destinées aux investisseurs.</li>
      <li>Les actions de type B (carried-interest) destinées à être souscrites par les personnes intervenant dans la gestion de Morvane Capital</li>
      <li>En vertu des dispositions légales et statutaires applicables, l'émission de 100 actions de type A oblige à émettre 1 action B Ne pouvant être souscrite que par les personnes intervenant dans la gestion de Morvane Capital.</li>
    </ul>
    <p class="abs justify" style="left:30px;top:472px;width:216px">Les droits préférentiels attachés aux actions A et aux actions B sont définis à l'article 14.2 des statuts de Morvane Capital et répondent notamment au principe selon lequel l'actif net de liquidation au-delà d'un "rendement" de 7% l'an sera réparti à hauteur de 80% pour les actions A (investisseurs) et 20% pour les actions B (personnes intervenant dans la gestion du fonds) aux types de catégorie d'actions A et B.</p>
    <p class="abs chart-title" style="left:262px;top:392px">Pertage des gains espérés</p>
    <div class="gain-bar abs" style="left:256px;top:405px;width:40px;height:57px">80%</div>
    <div class="gain-bar abs" style="left:298px;top:430px;width:40px;height:32px">20%</div>
    <div class="gain-label abs" style="left:256px;top:462px;width:40px;height:16px">Investisseur</div>
    <div class="gain-label abs" style="left:298px;top:462px;width:40px;height:16px">Gestionnaire</div>
    <div class="gain-class abs" style="left:256px;top:482px;width:40px;height:12px">ACTIONS A</div>
    <div class="gain-class abs" style="left:298px;top:482px;width:40px;height:12px">ACTIONS B</div>
  </section>

  <section class="panel panel-4">
    <h2 class="abs" style="left:16px;top:14px;width:390px">Risques liés à l'investissement dans Morvane Capital</h2>
    <p class="abs bold" style="left:16px;top:28px;font-size:5.6px">Facteurs de risques liés à l'investissement dans Morvane Capital :</p>
    <p class="abs justify" style="left:16px;top:40px;width:390px">Rien ne garantit la rentabilité de l'investissement au capital de la Société, ni même la récupération de tout ou partie de la mise de fonds initiale. La réalisation de tout ou partie de ces risques est susceptible d'avoir un effet négatif sur les activités, la situation, les résultats financiers de la Société ou ses objectifs.</p>
    <div class="abs justify" style="left:16px;top:62px;width:192px">
      <p><span class="risk-title">Risques liés à l'application du régime des SCR</span> La Société Morvane Capital ayant opté pour le régime des sociétés de capital-risque ayant pour objet exclusif la gestion d'un portefeuille de valeurs mobilières et de titres non cotés bénéficiera d'un statut fiscal privilégié. En contrepartie, elle s'engage à respecter certaines conditions, et notamment les quotas de titres éligibles définis par l'article 1er de la loi n°85-695 du 11 juillet 1985.</p>
      <p style="margin-top:6px">À cet égard, la société Morvane Capital a pris la précaution d'obtenir une opinion fiscale de la part du cabinet d'avocats Maréval &amp; Associés. Si les investissements envisagés ont bien entendu été paramétrés afin de respecter les critères d'éligibilité imposés par ces dispositions, la Société ne peut garantir qu'elle ne sera pas amenée à renoncer à la réalisation d'un investissement, ou à devoir céder par anticipation une ou plusieurs participations, de manière à conserver le bénéfice de ce régime.</p>
      <p style="margin-top:6px">Il est par ailleurs souligné qu'une SCR ne peut recourir à l'emprunt que dans la limite de 10 % de son actif net comptable, ce qui empêche la société Morvane Capital de disposer d'une importante réserve de financement en cas de nécessité. La société pourra donc ne pas être en mesure de participer à un investissement si ses ressources propres ne sont pas suffisantes pour financer celui-ci.</p>
      <p style="margin-top:6px">Du fait de son statut de SCR, la société Morvane Capital sera systématiquement minoritaire (seuil de détention inférieur à 40% des droits de vote) au capital des sociétés devant être retenues dans son quota d'investissement et ne sera pas impliquée dans les décisions de gestion quotidienne. Par contre, la société pourra veiller à obtenir un pacte d'actionnaires qui lui permettra de disposer de prérogatives de contrôle de ses investissements et ainsi prendre part aux décisions importantes de la gestion des participations.</p>
      <p style="margin-top:6px">Bien que l'option pour ce régime implique que la société apporte la plus grande attention au respect des contraintes auxquelles il est subordonné, le non-respect de certaines conditions pourra entraîner la perte du régime fiscal de SCR et, par voie de conséquence, la perte rétroactive des avantages fiscaux dont ont bénéficié les actionnaires.</p>
      <p style="margin-top:6px">En outre, le régime juridique et fiscal des SCR a subi dans le passé de fréquentes modifications. La Société ne peut donc garantir qu'elle ne sera pas soumise à des contraintes de gestion supplémentaires par rapport à celles existantes à la date d'établissement du présent document d'information, que le régime fiscal applicable à ses actionnaires restera inchangé, ni que ses investissements en conserveront le bénéfice de ce régime fiscal de faveur.</p>
    </div>
    <div class="abs justify" style="left:218px;top:62px;width:188px">
      <p>Ainsi, des modifications légales, fiscales et réglementaires peuvent intervenir et sont susceptibles d'affecter défavorablement la société Morvane Capital, les sociétés de son portefeuille ou ses actionnaires.</p>
      <p style="margin-top:5px"><span class="risk-title">Risque de perte en capital :</span> lié au risque de perte totale ou partielle d'investissement comme tout investissement au capital d'une société.</p>
      <p style="margin-top:5px"><span class="risk-title">Risque de dépendance au Groupe Ostral Outremer :</span> du fait de la participation active du Groupe Ostral Outremer aux choix des projets hôteliers dans lesquels pourrait investir la Société. La révocation du président désigné dans les statuts de la Société requiert la majorité des voix des associés présents ou représentés, sur un quorum de la moitié des actions.</p>
      <p style="margin-top:5px"><span class="risk-title">Risques inhérents à l'absence de comptes historiques de la Société :</span> du fait de la difficulté pour la Société à s'engager sur des données prévisionnelles chiffrées et sur sa capacité à générer des résultats, du fait de l'absence d'activité passée et de comptes historiques.</p>
      <p style="margin-top:5px"><span class="risk-title">Risque d'illiquidité :</span> lié au fait que les actifs dans lesquels la Société investira sont peu ou pas liquides et que la Société puisse éprouver des difficultés à céder ses participations dans les délais et les niveaux de prix souhaités.</p>
      <p style="margin-top:5px"><span class="risk-title">Risque d'estimation de la valeur des sociétés du portefeuille :</span> quels que soient la prudence et le soin apportés à ces évaluations, elles sont susceptibles de ne pas refléter la valeur exacte du portefeuille. De même, il ne peut être exclu que les sociétés du portefeuille soient cédées à un prix inférieur à celui auquel leurs titres auront été évalués.</p>
      <p style="margin-top:5px"><span class="risk-title">Risque lié à l'activité des sociétés du portefeuille :</span> les activités développées par les sociétés du portefeuille peuvent rétrospectivement avoir fait l'objet d'une analyse erronée des opportunités de marché par les dirigeants et ne pas rencontrer le succès commercial escompté.</p>
      <p style="margin-top:5px"><span class="risk-title">Risques liés à la variabilité du capital :</span> chaque associé de la Société peut se retirer de la société, du fait de la variabilité de son capital, lorsqu'il le juge convenable, sous réserve des dispositions légales et statutaires applicables, et notamment de la période de conservation telle que définie dans les statuts et qui s'étend de la souscription au 1er janvier 2019 au plus tôt. Aucune liquidité n'est garantie et les demandes de rachat seront traitées selon les règles statutaires de la Société.</p>
    </div>
    <h3 class="abs" style="left:54px;top:446px">Typologie des frais</h3>
    <table class="fees abs" style="left:14px;top:464px">
      <tr><td></td><td></td><td></td></tr>
      <tr><td></td><td></td><td></td></tr>
      <tr><td></td><td></td><td></td></tr>
      <tr><td></td><td></td><td></td></tr>
      <tr><td></td><td></td><td></td></tr>
      <tr><td></td><td></td><td></td></tr>
    </table>
    <h2 class="abs" style="left:250px;top:384px">Modalité de souscription</h2>
    <ul class="bullets abs" style="left:250px;top:406px;width:160px">
      <li style="margin-bottom:6px">Souscription minimale : 100.000€</li>
      <li style="margin-bottom:6px">Valeur nominale de l'action (hors prime d'émission) : 1,00€</li>
      <li style="margin-bottom:6px">Objectif de souscription : 30 millions d'euros au 31 décembre 2014</li>
      <li style="margin-bottom:6px">Période de conservation des actions : de la souscription au 1er janvier 2019 au plus tôt</li>
      <li style="margin-bottom:6px">Plafond de souscription : 30 % au plus des droits dans les bénéfices de la société Morvane Capital pour les associés personnes physiques (voir note annexe)</li>
      <li style="margin-bottom:6px">Souscription et cessions soumises à agrément conformément aux dispositions de l'article 13 des statuts de la société Morvane Capital</li>
    </ul>
  </section>

</div>
</body>
</html>
```